Verodex business card

Business card for sustainable investment company called "Verodex". Verodex is an exchange platform selling carbon credits between buyers and sellers. Carbon Credits are an environmental commodity for reducing global carbon emissions.

the card should obviously have our logo and the theme should be sustainability/environment mixed with a trading platform.

Contact Information for Business Card

Logo, Name, Title, Phone, Email

Colors
0054AA
0677BA
7BADD7
CADEEF
E8F1F8
0094D4
00A9DD
6FCCEA
C7EBF8
E9F6FB
00AB8E
00BBA5
67D7C9
C6EFE9
E9F9F6
59FF00
82FF00
B8FF75
E3FFCB
F4FFEA

```html
<!DOCTYPE html>
<html lang="en">
<head>
<meta charset="utf-8">
<title>Verodex business card</title>
<link rel="stylesheet" href="https://fonts.googleapis.com/css2?family=Open+Sans:wght@400;600;700;800&display=swap">
<style>
  :root {
    --page: #2a2d32;
    --navy: #132a52;
    --accent: #5fb6e0;
    --accent-deep: #4a86cc;
    --text-light: #ffffff;
    --rule: #8fa3c4;
    --face-top: #66cfdc;
    --face-bottom: #4a7bc6;
    --ink: #1b1d22;
  }
  * { margin: 0; padding: 0; box-sizing: border-box; }
  html, body {
    width: 1200px; height: 780px; overflow: hidden;
    background: var(--page);
    font-family: "Open Sans", Arial, sans-serif;
  }
  .sheet {
    width: 1200px; height: 780px;
    display: flex; align-items: center; justify-content: center; gap: 40px;
  }
  .card {
    width: 560px; height: 320px; position: relative; overflow: hidden;
    box-shadow: 0 12px 30px rgba(0,0,0,.45);
  }
  /* back side */
  .card--back { background: var(--navy); color: var(--text-light); }
  .back-brand {
    position: absolute; left: 36px; top: 118px;
    display: flex; align-items: center; gap: 12px;
  }
  .back-brand__dot {
    width: 22px; height: 22px; border-radius: 50%; background: var(--accent);
  }
  .back-brand__name {
    font-size: 40px; font-weight: 700; color: var(--accent); letter-spacing: .5px;
  }
  .back-rule { position: absolute; left: 0; top: 0; }
  .contact {
    position: absolute; left: 300px; top: 70px;
  }
  .contact__name {
    font-size: 26px; font-weight: 700; color: var(--accent); line-height: 1.1;
  }
  .contact__title {
    font-size: 15px; font-weight: 600; margin: 4px 0 14px;
  }
  .contact__address { font-size: 13.5px; line-height: 1.4; margin-bottom: 14px; }
  .contact__line {
    display: flex; align-items: center; gap: 8px;
    font-size: 13.5px; line-height: 1.5;
  }
  .contact__line svg { width: 13px; height: 13px; flex: none; }
  /* front side */
  .card--front {
    background: linear-gradient(150deg, var(--face-top) 0%, var(--face-bottom) 100%);
    display: flex; align-items: center; justify-content: center;
  }
  .front-brand { display: flex; align-items: center; gap: 16px; }
  .front-brand__mark { width: 34px; height: 34px; background: var(--ink); }
  .front-brand__name {
    font-size: 54px; font-weight: 800; color: var(--ink); letter-spacing: 1px;
  }
</style>
</head>
<body>
<main class="sheet">
  <section class="card card--back" aria-label="Card back with contact details">
    <div class="back-brand">
      <span class="back-brand__dot"></span>
      <span class="back-brand__name">Verodex</span>
    </div>
    <svg class="back-rule" width="560" height="320" aria-hidden="true">
      <line x1="278" y1="58" x2="278" y2="262" stroke="var(--rule)" stroke-width="1"/>
    </svg>
    <div class="contact">
      <p class="contact__name">Lena Marvik</p>
      <p class="contact__title">Managing Director</p>
      <p class="contact__address">4870 Harbor Lane, Suite 310<br>Dayton, OH 45402</p>
      <p class="contact__line">
        <svg viewBox="0 0 16 16" aria-hidden="true"><path fill="var(--accent)" d="M3.5 1.5l2.6 0 1 3.2-1.6 1.2a8 8 0 0 0 4.6 4.6l1.2-1.6 3.2 1v2.6c0 .8-.7 1.5-1.5 1.5A12.5 12.5 0 0 1 2 3c0-.8.7-1.5 1.5-1.5z"/></svg>
        (555) 204-6139
      </p>
      <p class="contact__line">
        <svg viewBox="0 0 16 16" aria-hidden="true"><rect x="1" y="3" width="14" height="10" rx="1.5" fill="var(--accent)"/><path d="M1.5 4l6.5 5 6.5-5" fill="none" stroke="var(--navy)" stroke-width="1.3"/></svg>
        info@verodex.com
      </p>
      <p class="contact__line">
        <svg viewBox="0 0 16 16" aria-hidden="true"><circle cx="8" cy="8" r="7" fill="var(--accent)"/><path d="M1 8h14M8 1c-3 3.5-3 10.5 0 14M8 1c3 3.5 3 10.5 0 14" fill="none" stroke="var(--navy)" stroke-width="1"/></svg>
        www.verodex.com
      </p>
    </div>
  </section>

  <section class="card card--front" aria-label="Card front with company name">
    <div class="front-brand">
      <span class="front-brand__mark"></span>
      <span class="front-brand__name">VERODEX</span>
    </div>
  </section>
</main>
</body>
</html>
```